Moravel Aesthetic Doctor

I require an elegant, luxurious looking business card for my aesthetic business. I am a doctor and that will set me aside from competitors. I am planning to provide home and spa based treatments to clients with high expectations. I have attached my logo.

```html
<!DOCTYPE html>
<html lang="en">
<head>
<meta charset="utf-8">
<title>Moravel Aesthetic Doctor – Business Card</title>
<link rel="stylesheet" href="https://fonts.googleapis.com/css2?family=Roboto:wght@300;400;500&display=swap">
<style>
  :root {
    --backdrop: #e6e7e8;
    --card-grey: #a7a9ab;
    --band-grey: #a9abad;
    --paper: #ffffff;
    --ink-grey: #9a9c9f;
    --brand-blue: #5bb8e6;
    --white: #ffffff;
  }
  * { box-sizing: border-box; margin: 0; padding: 0; }
  html, body {
    width: 1200px; height: 1124px; overflow: hidden;
    background: var(--backdrop);
    font-family: "Roboto", Arial, sans-serif;
  }
  .canvas { position: relative; width: 1200px; height: 1124px; }

  .card {
    position: absolute; left: 170px; width: 860px; height: 490px;
    box-shadow: 0 6px 18px rgba(0,0,0,.18);
    overflow: hidden;
  }
  .card--back { top: 40px; background: var(--card-grey); }
  .card--front { top: 594px; background: var(--paper); }

  /* Wordmark */
  .wordmark { display: flex; align-items: center; gap: 22px; }
  .wordmark__dot {
    width: 92px; height: 92px; border-radius: 50%;
    background: var(--brand-blue);
  }
  .wordmark__text { font-weight: 300; color: var(--brand-blue); line-height: 1; }
  .wordmark__name { display: block; font-size: 66px; letter-spacing: 4px; text-transform: uppercase; }
  .wordmark__tag { display: block; font-size: 24px; letter-spacing: 3px; text-transform: uppercase; margin-top: 8px; }

  .card--back .wordmark { position: absolute; top: 110px; left: 0; right: 0; justify-content: center; }
  .card--back .wordmark__text { color: var(--white); }
  .card--back .wordmark__dot { background: var(--white); }

  .services {
    position: absolute; top: 290px; left: 0; right: 0;
    text-align: center; color: var(--white);
    font-size: 23px; font-weight: 300; line-height: 1.45;
  }

  .card--front .wordmark { position: absolute; top: 56px; left: 0; right: 0; justify-content: center; }

  .name-band {
    position: absolute; top: 190px; left: 0; right: 0; height: 96px;
    background: var(--band-grey); color: var(--white); text-align: center;
    padding-top: 14px;
  }
  .name-band__name { font-size: 30px; font-weight: 500; }
  .name-band__creds { font-size: 18px; font-weight: 500; }
  .name-band__title { font-size: 22px; font-weight: 300; margin-top: 4px; letter-spacing: .5px; }

  .social { position: absolute; top: 334px; left: 0; right: 0; display: flex; justify-content: center; gap: 16px; }
  .social__dot { width: 30px; height: 30px; border-radius: 50%; background: var(--brand-blue); }

  .contacts {
    position: absolute; top: 386px; left: 0; right: 0;
    display: flex; justify-content: center; gap: 38px;
    color: var(--ink-grey); font-size: 23px; font-weight: 300;
  }
  .contact { display: flex; align-items: center; gap: 12px; }
  .contact svg { width: 20px; height: 20px; fill: none; stroke: var(--brand-blue); stroke-width: 1.6; }
  .contact svg .solid { fill: var(--brand-blue); stroke: none; }
  .accent { color: var(--brand-blue); }
</style>
</head>
<body>
<main class="canvas">

  <section class="card card--back" aria-label="Business card back">
    <div class="wordmark">
      <span class="wordmark__dot"></span>
      <span class="wordmark__text">
        <span class="wordmark__name">Moravel</span>
        <span class="wordmark__tag">Aesthetic Doctor</span>
      </span>
    </div>
    <p class="services">
      Dermal injectables • Plasma facials • Microneedling<br>
      Skin boosters • Excessive sweating<br>
      Home and Spa Based Treatments
    </p>
  </section>

  <section class="card card--front" aria-label="Business card front">
    <div class="wordmark">
      <span class="wordmark__dot"></span>
      <span class="wordmark__text">
        <span class="wordmark__name">Moravel</span>
        <span class="wordmark__tag">Aesthetic Doctor</span>
      </span>
    </div>

    <div class="name-band">
      <p><span class="name-band__name">Dr Lena Marwick,</span> <span class="name-band__creds">MRCPCH MD</span></p>
      <p class="name-band__title">Australasian Diploma of Aesthetic Medicine</p>
    </div>

    <div class="social" aria-label="Social media">
      <span class="social__dot"></span>
      <span class="social__dot"></span>
    </div>

    <div class="contacts">
      <span class="contact">
        <svg viewBox="0 0 20 20" aria-hidden="true"><path class="solid" d="M5 2l3 3-2 2.5c1 2.2 2.6 3.8 4.5 4.5L13 10l3 3-2 3C8 16 4 12 3 5z"/></svg>
        0800 454 918
      </span>
      <span class="contact">
        <svg viewBox="0 0 20 20" aria-hidden="true"><rect x="2" y="5" width="16" height="11" rx="1"/><path d="M2.5 5.5L10 11l7.5-5.5"/></svg>
        lena@moravel.co.nz
      </span>
      <span class="contact">
        <svg viewBox="0 0 20 20" aria-hidden="true"><circle cx="10" cy="10" r="8"/><ellipse cx="10" cy="10" rx="3.5" ry="8"/><path d="M2 10h16M3.5 6h13M3.5 14h13"/></svg>
        <span>www.<span class="accent">moravel</span>.co.nz</span>
      </span>
    </div>
  </section>

</main>
</body>
</html>
```